Business Card: RW Office Partners - Your organised problem solver

Business Name: RW Office Partners
Website: www.rwofficepartners.com.au
Email: marisol@rwofficepartners.com.au
Mobile: 61 482 907 236
Facebook: @rwofficepartners
Instrgram: @rwofficepartners

Brading Colours:
HEX
#986474
#ddccd3
#7a8498
#c9d8e4
#000000
#ffffff

Tag Line: Your organised problem solver

Link to DRAFT website:
https://deskhelpcollective.wixsite.com/rw-office-partners

About Page from the website:
My name is Marisol Wrenfield, and I would love to assist you to become more productive in your day to day and achieve your business and personal goals.
My mission is to give you time, time to work on the important tasks of your business or to be able to spend more time with your family. I will take on the tasks you don’t have time for, don’t know well or simply don’t like to do.
I have an extensive background in Administration, Tender Coordination, Document Control, WHS and Quality Management working primarily in the Construction, Mining and Corporate World.
I am passionate about being organised, having order and making things in your life (and mine) easier! I love to watch something unfold and grow into something amazing! I am known for being the go-to problem solver, the organiser of all things, producing high standards of work even under pressure. I’m also a confident communicator, and I understand that you’re busy running your business.

Target Market(s)

Small to Medium Business who require assistance in their business by a virtual assistant.

Industry/Entity Type

Virtual Assistant

Contact Information for Business Card

Mobile: 61 482 907 236

Font styles to use
Sans Serif

Colors
ffffff

Requirements
Must have
• Branding Colours as outlined.
Contact Details as outlined.
Logo as provided.
Proper contact details - mobile, facebook, instragm, website.
Simple, Elegant, very clean looking.
Should not have
• Note cute with pictures.
Not too girly as still want to market to construction companies.

```html
<!DOCTYPE html>
<html lang="en">
<head>
<meta charset="utf-8">
<title>RW Office Partners – Business Card</title>
<link href="https://fonts.googleapis.com/css2?family=Montserrat:wght@500&family=Roboto:wght@400&display=swap" rel="stylesheet">
<style>
  :root {
    --page: #e6e6e9;
    --card: #1f1f21;
    --pattern: #262628;
    --rose: #986474;
    --slate: #a9b2c4;
    --slate-deep: #7a8498;
  }
  * { margin: 0; padding: 0; box-sizing: border-box; }
  html, body { width: 1200px; height: 900px; overflow: hidden; }
  body {
    background: var(--page);
    position: relative;
    font-family: "Roboto", Arial, sans-serif;
  }
  .card {
    position: absolute;
    left: 320px;
    width: 560px;
    height: 320px;
    background: var(--card);
    border-radius: 4px;
    box-shadow: 0 10px 28px rgba(0,0,0,0.22);
    overflow: hidden;
  }
  .card--front { top: 100px; }
  .card--back { top: 480px; }

  .brand {
    position: absolute;
    left: 56px;
    top: 48px;
    display: flex;
    align-items: center;
    gap: 12px;
  }
  .brand__mark {
    width: 14px;
    height: 14px;
    background: var(--rose);
  }
  .brand__name {
    font-family: "Montserrat", Arial, sans-serif;
    font-weight: 500;
    font-size: 26px;
    letter-spacing: 1px;
    text-transform: uppercase;
    color: var(--slate);
  }

  .contacts {
    position: absolute;
    left: 56px;
    top: 126px;
    list-style: none;
  }
  .contacts__item {
    display: flex;
    align-items: center;
    gap: 8px;
    font-size: 15px;
    line-height: 26px;
    color: var(--slate);
  }
  .contacts__icon { width: 13px; height: 13px; flex: none; }
  .contacts__icon path, .contacts__icon circle, .contacts__icon rect { fill: var(--rose); }
  .contacts__social { display: flex; gap: 4px; }
  .contacts__social span { width: 12px; height: 12px; background: var(--rose); border-radius: 2px; }

  .tagline {
    position: absolute;
    left: 56px;
    top: 250px;
    font-size: 15px;
    color: var(--rose);
  }

  .back__pattern {
    position: absolute;
    inset: 0;
    background: var(--pattern);
  }
  .back__name {
    position: absolute;
    right: 40px;
    bottom: 34px;
    font-family: "Montserrat", Arial, sans-serif;
    font-weight: 500;
    font-size: 20px;
    text-transform: uppercase;
    letter-spacing: 1px;
    color: var(--rose);
  }
</style>
</head>
<body>

<section class="card card--front">
  <div class="brand">
    <span class="brand__mark"></span>
    <span class="brand__name">RW Office Partners</span>
  </div>

  <ul class="contacts">
    <li class="contacts__item">
      <svg class="contacts__icon" viewBox="0 0 16 16"><path d="M3.5 1l3 3-1.8 1.8a9 9 0 0 0 5.5 5.5L12 9.5l3 3-2 2.5C6.5 14.5 1.5 9.5 1 3z"/></svg>
      61 482 907 236
    </li>
    <li class="contacts__item">
      <svg class="contacts__icon" viewBox="0 0 16 16"><rect x="1" y="3" width="14" height="10" rx="1"/></svg>
      marisol@rwofficepartners.com.au
    </li>
    <li class="contacts__item">
      <svg class="contacts__icon" viewBox="0 0 16 16"><circle cx="8" cy="8" r="7"/></svg>
      www.rwofficepartners.com.au
    </li>
    <li class="contacts__item">
      <span class="contacts__social"><span></span><span></span></span>
      @rwofficepartners
    </li>
  </ul>

  <p class="tagline">Your organised problem solver</p>
</section>

<section class="card card--back">
  <div class="back__pattern" role="img" aria-label="Subtle tone-on-tone repeating brand monogram pattern"></div>
  <span class="back__name">RW Office Partners</span>
</section>

</body>
</html>
```